Visitenkarten-Design für Steuerberater und Wirtschaftsprüfer
Thank you so much! Great communication, very fast and nice contact!
Zielgruppe
Steuerberater, Wirtschaftsprüfer in München
Aufgabenstellung
Wir haben ein Logo das uns gefällt, jetzt allerdings steht die Umfirmierung vor der Tür und aus der Kanzlei Zelliger (so unser Name) wird Zelliger und Partner mbB (die Jugend kommt mit als Partner in die Kanzlei) , Steuerberater, Wirtschaftsprüfer
Analog unseres alten Briefpapiers und der alten Visitenkarten soll eigentlich nur der Zusatz 'und Partner mbB' oder '& Partner mbB' gestaltet werden.
Das Dateiformat bei Visitenkarten bitte so übergeben, dass wir Namen selbst austauschen mit gängigen Officeprogrammen austauschen können. Bei den Visitenkarten ist das große 'Zelliger' geprägt.
Ich stelle das Logo, das aktuelle Briefpapier und aktuelle Visitenkarten ein. Unsere Farbe ist grau.
Das Logo bitte in .pdf, .png, .psd und .eps (sagt mi alles nichts, haben wir aber alles schon mal irgendwo gebraucht) , Visiten karten auch in .pddf und .ai
Bei Fragen kontaktiert mich gern jederzeit.

```html
<!DOCTYPE html>
<html lang="de">
<head>
<meta charset="utf-8">
<title>Briefpapier Zelliger &amp; Partner mbB</title>
<link href="https://fonts.googleapis.com/css2?family=Arimo:wght@400;700&family=Tinos&family=Roboto+Condensed:wght@400;700&display=swap" rel="stylesheet">
<style>
  :root {
    --stage: #2b2b2b;
    --paper: #ffffff;
    --band: #d0d0d1;
    --ink: #1a1a1a;
    --brand: #6b6b6b;
    --muted: #8a8a8a;
    --guide: #d0202a;
  }
  html, body { margin: 0; padding: 0; overflow: hidden; }
  body { width: 1101px; height: 1200px; background: var(--stage); position: relative; }
  .sheet { position: absolute; left: 137px; top: 28px; width: 816px; height: 1142px; background: var(--paper); }
  .abs { position: absolute; }
  .band { position: absolute; background: var(--band); }
  .band--head-left { left: 0; top: 47px; width: 277px; height: 52px; }
  .band--head-right { left: 531px; top: 47px; width: 285px; height: 52px; }
  .band--foot-left { left: 0; top: 1098px; width: 97px; height: 42px; }
  .band--foot-right { left: 719px; top: 1098px; width: 97px; height: 42px; }
  .brand { position: absolute; left: 278px; top: 36px; width: 260px; text-align: center; color: var(--brand); font-family: Arimo, sans-serif; white-space: nowrap; }
  .brand__name { font-size: 37px; letter-spacing: 2px; line-height: 34px; }
  .brand__line { font-size: 25px; line-height: 24px; letter-spacing: .5px; }
  .brand__tag { font-size: 11px; letter-spacing: .2px; line-height: 13px; }
  .guide-v { left: 97px; top: 0; width: 1px; height: 212px; background: var(--guide); }
  .guide-h { height: 1px; background: var(--guide); }
  .note { font-family: Tinos, serif; color: var(--guide); font-size: 15px; line-height: 20px; }
  .sender { left: 97px; top: 193px; font-family: "Roboto Condensed", sans-serif; font-size: 8.7px; color: var(--muted); white-space: nowrap; }
  .sender b { color: #555; }
  .text { font-family: Arimo, sans-serif; color: var(--ink); font-size: 15px; line-height: 19.3px; }
  .address { left: 97px; top: 209px; }
  .date { right: 98px; top: 349px; white-space: nowrap; }
  .subject { left: 97px; top: 384px; font-size: 19px; font-weight: 700; }
  .body { left: 97px; top: 445px; width: 615px; }
  .body p { margin: 0 0 19.3px; }
  .dot { width: 3px; height: 3px; border-radius: 50%; background: #999; left: 20px; }
  .footer { left: 0; top: 1096px; width: 816px; text-align: center; font-family: "Roboto Condensed", sans-serif; font-size: 12.5px; line-height: 15px; color: var(--muted); white-space: nowrap; }
  .footer b { color: #555; }
</style>
</head>
<body>
<main class="sheet">
  <div class="band band--head-left"></div>
  <div class="band band--head-right"></div>
  <div class="brand">
    <div class="brand__name">ZELLIGER</div>
    <div class="brand__line">&amp; PARTNER mbB</div>
    <div class="brand__tag">STEUERBERATER | WIRTSCHAFTSPRÜFER</div>
  </div>

  <div class="abs guide-v"></div>
  <div class="abs note" style="left:106px;top:125px;">55 mm</div>
  <div class="abs note" style="left:25px;top:192px;">25 mm</div>
  <div class="abs guide-h" style="left:0;top:213px;width:97px;"></div>
  <div class="abs note" style="left:743px;top:192px;">25 mm</div>
  <div class="abs guide-h" style="left:719px;top:213px;width:97px;"></div>
  <div class="abs note" style="left:25px;top:654px;">25 mm</div>
  <div class="abs guide-h" style="left:0;top:676px;width:97px;"></div>
  <div class="abs note" style="left:743px;top:654px;">25 mm</div>
  <div class="abs guide-h" style="left:719px;top:676px;width:97px;"></div>

  <div class="abs sender"><b>KANZLEI LORENZ H. ZELLIGER</b> | Lindenhofstr. 22 | 80331 München</div>

  <div class="abs text address">Musterfirma<br>Max Mustermann<br>Adresszusatz<br>Musterstraße 123<br>12345 Musterstadt<br>Musterland</div>

  <svg class="abs" style="left:232px;top:262px;" width="80" height="12" viewBox="0 0 80 12" aria-hidden="true">
    <line x1="8" y1="6" x2="80" y2="6" stroke="#d0202a" stroke-width="1.2"/>
    <polygon points="0,6 9,2 9,10" fill="#d0202a"/>
  </svg>
  <div class="abs note" style="left:315px;top:249px;">Anschriftenfeld:<br>75mm breit, 30mm hoch<br>Schrift: Arial, 11pt, 6 mögliche<br>Zeilen</div>

  <div class="abs text date">München, 00. Monat 2014</div>
  <div class="abs dot" style="top:376px;"></div>
  <div class="abs text subject">Betreffzeile</div>

  <div class="abs text body">
    <p>Sehr geehrter Herr Mustermann,</p>
    <p>Kurzer Brief an ein Idol. Lieber Onkel Reinhard, schon lange wollte ich Dir sagen, daß ich Dich für einen ganz tollen Texter halte. Ich weiß, Du hörst sehr gerne Lob, und deshalb kann man nicht oft genug sagen, daß Du der Größte bist.</p>
    <p>Gerade in Deinem Alter ist man ja gesegnet, wenn man noch so witzig schreiben kann wie Du. Viele Deiner Werberkollegen sind ja schon zu wichtig, um noch den Humor zu haben.</p>
    <p>Du bist da ganz anders. Du kannst richtig komisch sein. Und das, obwohl Du in Deinem sehr langen Leben auch schon sehr viele unangenehme Dinge schreiben mußtest. Texte für Burgerhaus zum Beispiel. Oder kleine Reime für Onkel Norbert. Nein, Du hast es wirklich nicht leicht gehabt. Und dann noch die Selbstdarstellung für Tante Ika.</p>
    <p>Gerade in Deinem Alter ist man ja gesegnet, wenn man noch so witzig schreiben kann wie Du. Viele Deiner Werberkollegen sind ja schon zu wichtig, um noch den Humor zu haben.</p>
    <p style="margin-top:38px;margin-bottom:58px;">Mit freundlichen Grüßen</p>
    <p>Vorname Name<br>Titel</p>
  </div>
  <div class="abs dot" style="top:576px;"></div>

  <svg class="abs" style="left:536px;top:764px;" width="12" height="80" viewBox="0 0 12 80" aria-hidden="true">
    <line x1="6" y1="8" x2="6" y2="80" stroke="#d0202a" stroke-width="1.2"/>
    <polygon points="6,0 2,9 10,9" fill="#d0202a"/>
  </svg>
  <div class="abs note" style="left:543px;top:852px;">Textfeld:<br>160mm breit,180mm hoch<br>Schrift: Arial, 11pt (Betreff 14pt bold)</div>

  <div class="band band--foot-left"></div>
  <div class="band band--foot-right"></div>
  <div class="abs footer">
    <b>KANZLEI LORENZ H. ZELLIGER</b> | Lindenhofstr. 22 | 80331 München<br>
    <b>fon</b> 089-41207730 | <b>fax</b> 089-41207731 | <b>mail</b> info@kanzlei-zelliger.com | <b>web</b> www.kanzlei-zelliger.com<br>
    <b>UstID</b> DE 284517093 | <b>IBAN</b> DE 48 1234 5678 0004 8812 55 | <b>BIC</b> ZLPADEM1XXX
  </div>
</main>
</body>
</html>
```